Storm Restoration Contractor needs a professional letterhead design

Looking for a professional letterhead design. Not looking for your cheapo MS Word standard ones that are readily available. Dont want it to be cookie cutter look like ones readily available online. We just recently changed our logo and want to freshen up all our documents. Our company handles restoring a property back to a pre-loss condition after a storm damages it. For example, wind, hail, flood, fire losses.

Target Market(s)

Property Owners, Homeowners, Property Owners, Commercial Property Owners, Property Management Companies

Industry/Entity Type

Construction Company

Requirements
Must have
• Professional, Use 1 of 2 logo options
• Storm Restoration, Roofing, Siding, Windows

```html
<!DOCTYPE html>
<html lang="en">
<head>
<meta charset="utf-8">
<title>Stormline Exteriors – Letterhead &amp; Folder</title>
<link rel="stylesheet" href="https://fonts.googleapis.com/css2?family=Mulish:wght@400;600;800&display=swap">
<style>
  :root {
    --backdrop: #e6eaec;
    --paper: #ffffff;
    --folder: #dcdcdc;
    --brand-blue: #1e7dc4;
    --footer-blue: #1b7cc2;
    --stripe-gray: #4f5256;
    --ink: #3a3a3a;
    --ink-soft: #555;
    --faint-mark: #e4eef7;
  }
  * { box-sizing: border-box; margin: 0; padding: 0; }
  html, body {
    width: 1200px; height: 784px; overflow: hidden;
    background: var(--backdrop);
    font-family: "Mulish", sans-serif;
  }
  .stage { position: relative; width: 1200px; height: 784px; }

  .sheet {
    position: absolute; top: 45px; width: 513px; height: 697px;
    border-radius: 12px; overflow: hidden;
  }
  .letterhead { left: 42px; background: var(--paper); }
  .folder { left: 634px; background: var(--folder); }

  .brand {
    position: absolute; display: flex; align-items: center; gap: 10px;
  }
  .brand-dot {
    width: 42px; height: 42px; border-radius: 50%;
    border: 5px solid var(--brand-blue);
  }
  .brand-name {
    color: var(--brand-blue); font-weight: 800;
    font-size: 19px; line-height: 20px; letter-spacing: 1px;
    text-transform: uppercase;
  }
  .letterhead .brand { left: 155px; top: 38px; }
  .folder .brand { left: 128px; top: 570px; }
  .folder .brand-dot { width: 46px; height: 46px; }
  .folder .brand-name { font-size: 21px; line-height: 22px; }

  .faint-mark { position: absolute; left: 250px; top: 380px; }

  .letter-body {
    position: absolute; left: 48px; top: 143px; width: 427px;
    color: var(--ink); font-size: 10.6px; line-height: 18.6px;
    text-align: justify; hyphens: auto;
  }
  .letter-body p + p { margin-top: 18.6px; }

  .signature { position: absolute; left: 383px; top: 584px; color: var(--ink); }
  .signature-name { font-size: 13px; }
  .signature-title { font-size: 9.5px; margin-top: 9px; color: var(--ink-soft); }

  .footer-band { position: absolute; left: 0; top: 0; }
  .contact {
    position: absolute; left: 20px; top: 625px; color: #fff;
    font-size: 6.6px; line-height: 13px;
  }
  .contact li { list-style: none; display: flex; align-items: center; gap: 5px; }
  .contact-icon { width: 6px; height: 6px; background: rgba(255,255,255,.45); border-radius: 1px; }
  .contact .address { font-weight: 600; }
  .contact .web { font-size: 8.4px; letter-spacing: 2px; font-weight: 600; margin-top: 1px; }

  .pocket-tab { position: absolute; right: 0; top: 170px; }
</style>
</head>
<body>
<main class="stage">

  <section class="sheet letterhead">
    <svg class="faint-mark" width="260" height="260" viewBox="0 0 260 260" aria-hidden="true">
      <circle cx="130" cy="130" r="118" fill="none" stroke="var(--faint-mark)" stroke-width="16"/>
    </svg>

    <div class="brand">
      <span class="brand-dot"></span>
      <span class="brand-name">Stormline<br>Exteriors</span>
    </div>

    <div class="letter-body">
      <p>Lorem ipsum dolor sit amet, consectetur adipiscing elit. Donec orci purus, luctus vitae dignissim eu, iaculis sed purus. Vivamus faucibus, ipsum nec aliquet viverra, leo mauris condimentum ligula, sit amet sagittis enim ligula quis arcu. Nam egestas tortor id nisi porttitor mattis. In tortor ante, ultricies in suscipit a, tempus non massa. Vivamus et auctor mi. Fusce vel massa nulla. Phasellus nec eros mauris, et scelerisque orci. Donec malesuada orci vitae nulla accumsan porta a id massa.</p>
      <p>Quisque accumsan iaculis magna sit amet fringilla. Maecenas consequat, magna eget tincidunt semper, odio nibh rutrum mi, id feugiat ante nisi eu risus. Vestibulum nunc orci, rhoncus a placerat in, ultricies in mi. Cras mattis varius eros, vel fringilla nisi suscipit eget. Quisque scelerisque sagittis nulla at porttitor. Mauris a justo et tellus interdum tristique. Sed id augue vitae urna euismod commodo aliquet a quam. Pellentesque arcu velit, cursus et malesuada ut, consequat et diam. Nullam erat sem, rhoncus id ullamcorper vitae, rhoncus et arcu. In ultricies ultricies nulla.</p>
      <p>Kut rutrum nisi iaculis at. Donec eu magna a metus ornare faucibus. Fusce aliquet faucibus ultricies. Morbi semper, est id tincidunt gravida, sem arcu adipiscing lacus, ac bibendum nulla leo eu purus. Quisque nec diam sed risus consectetur a ccumsan quis quis nibh. Vestibulum id purus lorem. Donec eu magna a metus ornare faucibus. Fusce aliquet faucibus ultricies. Morbi semper, est id tincidunt gravida, sem arcu adipiscing lacus, ac bibendum nulla leo eu purus. Quisque nec diam sed risus consectetur a ccumsan quis quis nibh. Vestibulum id purus lorem.</p>
    </div>

    <div class="signature">
      <div class="signature-name">Dale Whitmore</div>
      <div class="signature-title">Co-Founder &amp; CEO</div>
    </div>

    <svg class="footer-band" width="513" height="697" viewBox="0 0 513 697" aria-hidden="true">
      <polygon points="0,595 513,662 513,676 0,603" fill="var(--stripe-gray)"/>
      <polygon points="0,603 513,676 513,697 0,697" fill="var(--footer-blue)"/>
    </svg>

    <ul class="contact">
      <li><span class="contact-icon"></span>(888) 555-0142</li>
      <li><span class="contact-icon"></span>(615) 555-0199</li>
      <li><span class="contact-icon"></span>info@stormlineexteriors.com</li>
      <li class="address">480 Harbor Point Drive, 2nd Floor, Maple Ridge, TN 37150</li>
      <li class="web">www.stormlineexteriors.com</li>
    </ul>
  </section>

  <section class="sheet folder">
    <svg class="pocket-tab" width="40" height="160" viewBox="0 0 40 160" aria-hidden="true">
      <path d="M40 0 C 22 4, 18 14, 18 30 L 18 160 L 40 160 Z" fill="#d6d6d6"/>
    </svg>
    <div class="brand">
      <span class="brand-dot"></span>
      <span class="brand-name">Stormline<br>Exteriors</span>
    </div>
  </section>

</main>
</body>
</html>
```